Business Card For Halvenmoor Financial Consulting

Hi, I would like a business card designed. Bold, modern.
Please use the same design as the logo. I have also attached the website design to see the overall theme.
Wordmark Font
Color: Hex: #01AEF7

```html
<!DOCTYPE html>
<html lang="en">
<head>
<meta charset="utf-8">
<title>Halvenmoor Financial Consulting – Business Card</title>
<link rel="stylesheet" href="https://fonts.googleapis.com/css2?family=Montserrat:wght@500;700&amp;family=Roboto:wght@400&amp;display=swap">
<style>
  :root {
    --backdrop: #3a3a3a;
    --card: #16202b;
    --accent: #01aef7;
    --accent-soft: #3d8fc4;
    --ink: #ffffff;
    --muted: #d9e2ea;
    --emboss: #233242;
  }
  * { box-sizing: border-box; margin: 0; padding: 0; }
  html, body {
    width: 1200px; height: 801px; overflow: hidden;
    background: var(--backdrop);
  }
  body {
    display: flex; align-items: center; justify-content: center; gap: 40px;
    font-family: "Roboto", Arial, sans-serif;
  }
  .card {
    position: relative;
    width: 540px; height: 309px;
    background: var(--card);
    border-bottom: 3px solid var(--accent);
    border-left: 2px solid var(--accent);
    color: var(--ink);
  }
  /* front */
  .brand {
    position: absolute; top: 44px; right: 40px;
    display: flex; align-items: center; gap: 10px;
  }
  .brand-square {
    width: 30px; height: 30px; border: 3px solid var(--accent-soft);
  }
  .brand-name {
    font-family: "Montserrat", Arial, sans-serif; font-weight: 700;
    font-size: 19px; letter-spacing: 0.5px; color: var(--ink);
    line-height: 1.15;
  }
  .person { position: absolute; left: 40px; top: 124px; }
  .person-name {
    font-family: "Montserrat", Arial, sans-serif; font-weight: 700;
    font-size: 20px; color: var(--accent); text-transform: uppercase;
  }
  .person-role { font-size: 14px; color: var(--muted); margin-top: 2px; }
  .divider {
    position: absolute; left: 40px; right: 40px; top: 186px;
    height: 1px; background: var(--accent);
  }
  .contacts {
    position: absolute; left: 40px; top: 204px;
    list-style: none; font-size: 13.5px; color: var(--muted);
  }
  .contacts li { display: flex; align-items: center; gap: 8px; margin-bottom: 6px; }
  .contacts svg { width: 11px; height: 11px; fill: var(--accent); flex: none; }
  .address {
    position: absolute; right: 40px; top: 204px;
    font-size: 13.5px; color: var(--muted); line-height: 1.5; font-style: normal;
  }
  /* back */
  .card-back { display: flex; align-items: center; justify-content: center; }
  .back-brand { display: flex; align-items: center; gap: 16px; }
  .back-square { width: 52px; height: 52px; border: 4px solid var(--emboss); }
  .back-name {
    font-family: "Montserrat", Arial, sans-serif; font-weight: 700;
    font-size: 30px; line-height: 1.15; color: var(--accent-soft);
  }
</style>
</head>
<body>
  <section class="card card-front">
    <div class="brand">
      <span class="brand-square"></span>
      <span class="brand-name">Halvenmoor Financial<br>Consulting</span>
    </div>
    <div class="person">
      <p class="person-name">Marcus Telvane</p>
      <p class="person-role">President</p>
    </div>
    <div class="divider"></div>
    <ul class="contacts">
      <li><svg viewBox="0 0 24 24"><path d="M6.6 10.8a15.1 15.1 0 0 0 6.6 6.6l2.2-2.2c.3-.3.7-.4 1-.2 1.1.4 2.3.6 3.6.6.6 0 1 .4 1 1V20c0 .6-.4 1-1 1A17 17 0 0 1 3 4c0-.6.4-1 1-1h3.5c.6 0 1 .4 1 1 0 1.3.2 2.5.6 3.6.1.3 0 .7-.2 1z"/></svg>555-301-7284</li>
      <li><svg viewBox="0 0 24 24"><path d="M2 5h20v14H2zm2 2v.5l8 5 8-5V7z"/></svg>info@HalvenmoorConsulting.com</li>
      <li><svg viewBox="0 0 24 24"><circle cx="12" cy="12" r="10"/></svg>www.HalvenmoorConsulting.com</li>
    </ul>
    <address class="address">18330 Cedar Cove Way<br>Larkport CA 90412</address>
  </section>

  <section class="card card-back">
    <div class="back-brand">
      <span class="back-square"></span>
      <span class="back-name">Halvenmoor Financial<br>Consulting</span>
    </div>
  </section>
</body>
</html>
```